HOT TUB - SPAS service needs an business card

I need an business for my company who his specialise in a maintenance,water treatment and cleaning of Hot Tub - Spas for commercial and residential customers. The company operate mainly in the ski resort of Chamonix, Megève and St Gervais. The final product should communicate pure water, cleanest and professional for luxury property's.
I have upload a logo but any improvement on it is welcome.(color,size, details etc..) or any other idea. Thank you
Company Name: 58 BAINS
My name: Lucien Marchetti
Email: lucimarch@examplemail.net
Tel: +33 (0)6 71 58 29 64
Description to be on the card in french(first langage) and in English:
- Spas service
- Entretien, traitement eau, nettoyage.
- Maintenance, water treatment, cleaning.
Industry/Entity Type
Residential
Colors
Designer to choose colors to be used in the design.
Look and feel
Each slider illustrates characteristics of the customer's brand and the style your logo design should communicate.

```html
<!DOCTYPE html>
<html lang="fr">
<head>
<meta charset="utf-8">
<title>58 BAINS — Business card</title>
<link rel="stylesheet" href="https://fonts.googleapis.com/css2?family=Source+Sans+3:wght@400;600;700&display=swap">
<style>
  :root {
    --page: #eef1f4;
    --water-light: #45b0f0;
    --water-mid: #2a95e2;
    --water-deep: #1a7fd3;
    --band: #0e63c6;
    --band-line: #a9dbff;
    --ink: #ffffff;
    --card-w: 736px;
    --card-h: 421px;
  }
  * { margin: 0; padding: 0; box-sizing: border-box; }
  html, body {
    width: 1200px;
    height: 939px;
    overflow: hidden;
    background: var(--page);
    font-family: "Source Sans 3", "Myriad Pro", Arial, sans-serif;
    color: var(--ink);
  }
  .canvas { position: relative; width: 1200px; height: 939px; }

  .card {
    position: absolute;
    width: var(--card-w);
    height: var(--card-h);
    border-radius: 30px;
    overflow: hidden;
    box-shadow: 0 3px 10px rgba(0, 0, 0, 0.18);
  }
  .card--front { left: 422px; top: 45px; }
  .card--back  { left: 55px;  top: 500px; }

  .card__art { position: absolute; inset: 0; width: 100%; height: 100%; }

  .brand-mark {
    position: absolute;
    display: flex;
    align-items: center;
    justify-content: center;
    gap: 14px;
    font-weight: 600;
    letter-spacing: 0.06em;
    color: var(--ink);
  }
  .brand-mark__dot {
    width: 16px; height: 16px;
    border-radius: 50%;
    background: var(--ink);
  }
  .card--front .brand-mark { left: 150px; top: 70px; width: 472px; height: 110px; font-size: 46px; }
  .card--back  .brand-mark { left: 92px;  top: 90px; width: 565px; height: 140px; font-size: 56px; }

  .company-name {
    position: absolute; left: 0; right: 0; top: 222px;
    text-align: center; font-size: 33px; font-weight: 600; letter-spacing: 0.01em;
  }
  .contact { position: absolute; left: 0; right: 0; text-align: center; }
  .contact__name  { top: 304px; font-size: 25px; font-weight: 700; }
  .contact__phone { top: 342px; font-size: 24px; font-weight: 600; }
  .contact__email { top: 380px; font-size: 23px; font-weight: 400; }
  .contact__icon { display: inline-block; vertical-align: -3px; margin-right: 10px; }

  .services { position: absolute; left: 0; right: 0; top: 292px; text-align: center; }
  .services__title { font-size: 27px; font-weight: 700; margin-bottom: 4px; }
  .services__list { font-size: 25px; font-weight: 400; line-height: 35px; }
</style>
</head>
<body>
<main class="canvas">

  <section class="card card--front" aria-label="Business card, front">
    <svg class="card__art" viewBox="0 0 736 421" preserveAspectRatio="none">
      <defs>
        <linearGradient id="waterFront" x1="0" y1="0" x2="1" y2="1">
          <stop offset="0" stop-color="var(--water-light)"/>
          <stop offset="0.55" stop-color="var(--water-mid)"/>
          <stop offset="1" stop-color="var(--water-deep)"/>
        </linearGradient>
      </defs>
      <rect width="736" height="421" fill="url(#waterFront)" role="img" aria-label="Blue surface covered with water droplets"/>
      <path d="M0,226 Q368,318 736,222" fill="none" stroke="var(--band-line)" stroke-width="9"/>
      <path d="M0,236 Q368,340 736,232 L736,421 L0,421 Z" fill="var(--band)"/>
    </svg>
    <div class="brand-mark"><span class="brand-mark__dot"></span>58 BAINS</div>
    <h1 class="company-name">58 BAINS</h1>
    <p class="contact contact__name">Lucien Marchetti</p>
    <p class="contact contact__phone">
      <svg class="contact__icon" width="20" height="22" viewBox="0 0 20 22" aria-hidden="true">
        <path d="M5 2 L8 6 L6 9 Q8 13 12 16 L15 14 L18 17 L15 20 Q5 18 2 6 Z" fill="none" stroke="#fff" stroke-width="1.8" stroke-linejoin="round"/>
      </svg>+33 (0)6 71 58 29 64
    </p>
    <p class="contact contact__email">
      <svg class="contact__icon" width="24" height="18" viewBox="0 0 24 18" aria-hidden="true">
        <rect x="1" y="5" width="22" height="12" rx="1.5" fill="#fff"/>
        <path d="M1 6 L12 13 L23 6" fill="none" stroke="var(--band)" stroke-width="1.6"/>
        <path d="M4 5 L12 0.8 L20 5" fill="#fff"/>
      </svg>lucimarch@examplemail.net
    </p>
  </section>

  <section class="card card--back" aria-label="Business card, back">
    <svg class="card__art" viewBox="0 0 736 421" preserveAspectRatio="none">
      <defs>
        <linearGradient id="waterBack" x1="0" y1="0" x2="1" y2="1">
          <stop offset="0" stop-color="var(--water-light)"/>
          <stop offset="0.55" stop-color="var(--water-mid)"/>
          <stop offset="1" stop-color="var(--water-deep)"/>
        </linearGradient>
      </defs>
      <rect width="736" height="421" fill="url(#waterBack)" role="img" aria-label="Blue surface covered with water droplets"/>
    </svg>
    <div class="brand-mark"><span class="brand-mark__dot"></span>58 BAINS</div>
    <div class="services">
      <h2 class="services__title">SPAS SERVICES</h2>
      <p class="services__list">• Entretien &nbsp;• traitement eau &nbsp;• nettoyage</p>
      <p class="services__list">• Maintenance &nbsp;• water treatment &nbsp;• cleaning.</p>
    </div>
  </section>

</main>
</body>
</html>
```